Bright and beautiful business card for a coach

I'm a personal and business coach based in Perth, Australia. I need a business card that whilst subtle and elegant, will stand out and appeal on a table full of cards.

My business name is Fern Mentoring and the business card must represent the warmth and brightness implied in the name, without being gimmicky. It must have a warmth and appeal and be easy to read.

I prefer clean, minimalist designs.

It must align with the feel of my website and socials: https://www.fernmentoring-example.com.au/
https://www.instagram.com/fernmentoringau/
https://www.facebook.com/fernmentoringau
Updates

Hi Designers Thank you so much for taking the time to submit designs. I wonder if I could have explained myself a little better. Most of the designs that have been submitted look rather formal and many have quite corporate looking embellishments on them (to my eye). I would like softer, warmer, more organic. I’m open to people playing about and being more abstract, using softer embellishments (e.g the line drawing flowers and grasses I’ve used in my socials) incorporating other colours from my palette or like the social icons in my email signature (in PDF), perhaps playing with size/oversize, playing with the bleed. Please don’t be constrained by what I’ve already done, it merely needs to compliment. I’m sorry if I’m not using the right words or have led you astray. I’m no designer, but I’ve done my website, socials, email signature etc all myself (my logo was a design contest) and I was really hoping for my business card to be something more creative than I could have made with a template. Reminder: No black cards/sides please. Thank you 😊

Target Market(s)

Individuals, most likely but not all female. Creative thinkers. Likely professionals.

Industry/Entity Type

Business & Personal Coach

Contact Information for Business Card

(Fern Mentoring Logo) Name: Greta Pellham; Title: Business & Personal Coach; Phone number: +61 (0)458 913307; Email: greta@fernmentoring-example.com.au; Website: https://fernmentoring-example.com.au; Social icons for Facebook, Instagram & LinkedIn: @fernmentoringAU. Optional strapline: "A thinking partner to help you cut through the noise"

Font styles to use
Sans Serif

Colors
00AB8E
00BBA5
67D7C9
C6EFE9
E9F9F6
59FF00
82FF00
B8FF75
E3FFCB
F4FFEA
FFC000
F8CF3A
FAE287
FDF2CF
FEFAEE

Requirements
Must have
• Must align with feel of my website and socials. Must have a pop of #FFC000 (possibly whole of one side, or at least a block). Bright or white background. Easy to read.
Nice to have
• Possibly incorporate the sunshine/grass picture I have used in website and socials - will upload.
Should not have
• Must not be black or dark. Not impersonal or corporate looking.

```html
<!DOCTYPE html>
<html lang="en">
<head>
<meta charset="utf-8">
<title>Fern Mentoring — Business Card</title>
<link rel="stylesheet" href="https://fonts.googleapis.com/css2?family=Lato:wght@400;700&display=swap">
<style>
  :root {
    --page: #eef0ec;
    --white: #ffffff;
    --gold: #e5a321;
    --gold-deep: #c9781f;
    --amber: #d68a1e;
    --ink: #555a5e;
    --rule: #b9bcbe;
    --grass-light: #c8df8a;
    --grass: #5f9a2c;
    --grass-dark: #2f5a1a;
    --glow: #f7e4cf;
  }
  * { box-sizing: border-box; margin: 0; padding: 0; }
  html, body { width: 1200px; height: 895px; overflow: hidden; }
  body {
    background: var(--page);
    font-family: "Lato", Arial, sans-serif;
    display: flex;
    align-items: center;
    justify-content: center;
    gap: 40px;
  }
  .card {
    width: 540px;
    height: 308px;
    position: relative;
    overflow: hidden;
    background: var(--white);
    box-shadow: 0 6px 18px rgba(0,0,0,0.12);
  }

  /* Front */
  .card-front .photo {
    position: absolute;
    inset: 0 0 58px 0;
    background:
      radial-gradient(circle at 58% 22%, var(--glow) 0%, rgba(247,228,207,0.6) 14%, rgba(247,228,207,0) 34%),
      linear-gradient(180deg, #9fae7a 0%, var(--grass) 45%, var(--grass-dark) 100%);
  }
  .card-front .wordmark {
    position: absolute;
    left: 0; right: 0;
    top: 100px;
    text-align: center;
    color: var(--white);
    font-weight: 400;
    font-size: 40px;
    letter-spacing: 6px;
  }
  .card-front .band {
    position: absolute;
    left: 0; right: 0; bottom: 0;
    height: 58px;
    background: linear-gradient(90deg, var(--gold-deep) 0%, var(--gold) 100%);
    display: flex;
    align-items: center;
    justify-content: center;
  }
  .card-front .strapline {
    color: var(--white);
    font-weight: 700;
    font-size: 13.5px;
    letter-spacing: 0.6px;
    text-transform: uppercase;
  }

  /* Back */
  .card-back .brand {
    position: absolute;
    left: 34px;
    top: 138px;
    display: flex;
    align-items: center;
    gap: 10px;
  }
  .card-back .brand-dot {
    width: 14px; height: 14px;
    border-radius: 50%;
    background: var(--gold);
  }
  .card-back .brand-name {
    color: var(--amber);
    font-weight: 400;
    font-size: 26px;
    letter-spacing: 2px;
  }
  .card-back .divider {
    position: absolute;
    left: 268px;
    top: 70px;
    width: 1px;
    height: 168px;
    background: var(--rule);
  }
  .card-back .contact {
    position: absolute;
    left: 288px;
    top: 72px;
    right: 10px;
    color: var(--ink);
  }
  .contact .name {
    color: var(--amber);
    font-weight: 700;
    font-size: 19px;
    line-height: 1.1;
  }
  .contact .title {
    font-size: 12.5px;
    margin-top: 3px;
    margin-bottom: 16px;
  }
  .contact .row {
    display: flex;
    align-items: center;
    gap: 8px;
    font-size: 11px;
    line-height: 1;
    margin-bottom: 7px;
    white-space: nowrap;
  }
  .contact .icon {
    width: 14px; height: 14px;
    border-radius: 50%;
    background: var(--gold);
    flex: none;
    display: flex;
    align-items: center;
    justify-content: center;
  }
  .contact .icon svg { width: 8px; height: 8px; }
  .contact .socials { margin-top: 10px; }
  .contact .social-dots { display: flex; gap: 4px; }
</style>
</head>
<body>
  <section class="card card-front">
    <div class="photo" role="img" aria-label="Sunlit close-up of green grass with soft morning sun glow"></div>
    <div class="wordmark">Fern Mentoring</div>
    <div class="band">
      <p class="strapline">A thinking partner to help you cut through the noise</p>
    </div>
  </section>

  <section class="card card-back">
    <div class="brand">
      <span class="brand-dot"></span>
      <span class="brand-name">Fern Mentoring</span>
    </div>
    <div class="divider"></div>
    <div class="contact">
      <p class="name">Greta Pellham</p>
      <p class="title">Business &amp; Personal Coach</p>
      <div class="row">
        <span class="icon"><svg viewBox="0 0 10 10"><path d="M2 1 L4 1 L4.6 3 L3.5 3.8 Q4.4 5.8 6.2 6.5 L7 5.4 L9 6 L9 8 Q5 9 2 5.5 Q1 3.5 2 1 Z" fill="#fff"/></svg></span>
        <span>+61 (0)458 913307</span>
      </div>
      <div class="row">
        <span class="icon"><svg viewBox="0 0 10 10"><rect x="1" y="2.5" width="8" height="5" fill="#fff"/><path d="M1 2.5 L5 5.5 L9 2.5" stroke="#e5a321" stroke-width="0.8" fill="none"/></svg></span>
        <span>greta@fernmentoring-example.com.au</span>
      </div>
      <div class="row">
        <span class="icon"><svg viewBox="0 0 10 10"><circle cx="5" cy="5" r="3.8" stroke="#fff" stroke-width="0.9" fill="none"/><path d="M1.2 5 H8.8 M5 1.2 V8.8" stroke="#fff" stroke-width="0.8"/></svg></span>
        <span>fernmentoring-example.com.au</span>
      </div>
      <div class="row socials">
        <span class="social-dots">
          <span class="icon"></span>
          <span class="icon"></span>
          <span class="icon"></span>
        </span>
        <span>@fernmentoringAU</span>
      </div>
    </div>
  </section>
</body>
</html>
```